KDWB Business Card

Looking for a business card design to incorporate our branding. We want to only use the colors listing in the Branding Package (attached).
Updates

Target Market(s)

People who need their phone or device fixed.

Industry/Entity Type

Electronics

Contact Information for Business Card

Please use:

Brightwick Gadget Clinic LLC
4810 E Harlow Ridge Rd
Suite 417
San Antonio, TX 78163

Marcus Delgrove, Store Manager

(210) 555-0147

Requirements
Must have
• Must include the colors that are contained within the Branding Package PDF file.

```html
<!DOCTYPE html>
<html lang="en">
<head>
<meta charset="utf-8">
<title>Brightwick Gadget Clinic – Business Card</title>
<link href="https://fonts.googleapis.com/css2?family=Roboto:wght@300;400;500&family=Arimo:wght@400&display=swap" rel="stylesheet">
<style>
  :root {
    --page-bg: #d9d9d7;
    --card-light: #f4f4f3;
    --card-mid: #e2e1de;
    --card-shade: #cfcdc8;
    --brand-red: #d9402a;
    --brand-red-dark: #b8321f;
    --ink: #1f1f1f;
    --band-dark: #121212;
    --band-grey: #3a3a3a;
    --mark-tint: rgba(232, 170, 140, 0.28);
  }
  html, body {
    margin: 0;
    padding: 0;
    width: 1200px;
    height: 1200px;
    overflow: hidden;
    background: var(--page-bg);
  }
  .card {
    position: absolute;
    left: 75px;
    top: 285px;
    width: 1050px;
    height: 630px;
    overflow: hidden;
    background:
      radial-gradient(ellipse at 30% 40%, var(--card-light) 0%, transparent 60%),
      linear-gradient(135deg, var(--card-light) 0%, var(--card-mid) 45%, var(--card-shade) 100%);
    box-shadow: 0 2px 6px rgba(0,0,0,0.18);
    font-family: "Roboto", sans-serif;
    color: var(--ink);
  }
  .brand-mark-faint {
    position: absolute;
    left: 555px;
    top: 45px;
    width: 470px;
    height: 495px;
    border-radius: 70px;
    background: var(--mark-tint);
  }
  .brand {
    position: absolute;
    left: 68px;
    top: 80px;
    display: flex;
    align-items: center;
    gap: 18px;
  }
  .brand-square {
    width: 86px;
    height: 86px;
    border-radius: 14px;
    background: var(--brand-red);
  }
  .brand-name {
    font-family: "Roboto", sans-serif;
    font-weight: 400;
    font-size: 36px;
    color: var(--brand-red);
    letter-spacing: 0.2px;
  }
  .person {
    position: absolute;
    left: 64px;
    top: 296px;
  }
  .person-name {
    font-size: 32px;
    font-weight: 400;
    letter-spacing: -0.3px;
    line-height: 1;
  }
  .person-title {
    margin-top: 8px;
    font-size: 18px;
    font-weight: 300;
    color: var(--brand-red);
  }
  .contact {
    position: absolute;
    left: 64px;
    top: 468px;
    font-family: "Arimo", sans-serif;
    font-size: 24px;
    letter-spacing: 0.4px;
  }
  .contact-row {
    display: flex;
    align-items: center;
    gap: 14px;
    height: 40px;
  }
  .contact-icon {
    width: 25px;
    height: 25px;
    flex: none;
  }
  .footer-band {
    position: absolute;
    left: 0;
    bottom: 0;
    width: 1050px;
    height: 54px;
  }
</style>
</head>
<body>
  <div class="card">
    <div class="brand-mark-faint" aria-hidden="true"></div>

    <div class="brand">
      <div class="brand-square" aria-hidden="true"></div>
      <div class="brand-name">Brightwick Gadget Clinic</div>
    </div>

    <div class="person">
      <div class="person-name">Marcus Delgrove</div>
      <div class="person-title">Store Manager</div>
    </div>

    <div class="contact">
      <div class="contact-row">
        <svg class="contact-icon" viewBox="0 0 25 25" aria-hidden="true">
          <rect width="25" height="25" fill="var(--brand-red)"/>
          <path d="M8 6 L11 6 L12 10 L10.3 11.2 C11.2 13.2 12.3 14.4 14 15.2 L15.2 13.6 L19 14.8 L19 18 C12.5 18.5 7 13 8 6 Z" fill="#fff"/>
        </svg>
        <span>(210) 555-0147</span>
      </div>
      <div class="contact-row">
        <svg class="contact-icon" viewBox="0 0 25 25" aria-hidden="true">
          <rect width="25" height="25" fill="var(--brand-red)"/>
          <path d="M12.5 5 C9.5 5 7.5 7.2 7.5 10 C7.5 13.5 12.5 20 12.5 20 C12.5 20 17.5 13.5 17.5 10 C17.5 7.2 15.5 5 12.5 5 Z" fill="#fff"/>
          <circle cx="12.5" cy="10" r="2.2" fill="var(--brand-red)"/>
        </svg>
        <span>4810 E Harlow Ridge Rd, Suite 417, San Antonio, TX 78163</span>
      </div>
    </div>

    <svg class="footer-band" viewBox="0 0 1050 54" aria-hidden="true">
      <defs>
        <linearGradient id="bandDark" x1="0" x2="1" y1="0" y2="0">
          <stop offset="0" stop-color="var(--band-grey)"/>
          <stop offset="0.5" stop-color="var(--band-dark)"/>
          <stop offset="1" stop-color="var(--band-dark)"/>
        </linearGradient>
        <linearGradient id="bandRed" x1="0" x2="1" y1="0" y2="0">
          <stop offset="0" stop-color="var(--brand-red-dark)"/>
          <stop offset="1" stop-color="var(--brand-red)"/>
        </linearGradient>
      </defs>
      <rect x="0" y="0" width="1050" height="54" fill="url(#bandDark)"/>
      <rect x="0" y="0" width="1050" height="3" fill="#555"/>
      <polygon points="0,14 488,14 505,54 0,54" fill="#f2f2f2"/>
      <polygon points="0,18 480,18 494,54 0,54" fill="url(#bandRed)"/>
    </svg>
  </div>
</body>
</html>
```